RWT Fittings Ltd Business Cards

We need a business card with our business logo. We provide window and door installations on high-rises in west coast British Colombia, Canada.

I would like my business information and details on one side of the card, and the other side the company name with logo

Target Market(s)

General Contractors

Industry/Entity Type

Construction

Contact Information for Business Card

one side i want my company name and logo in the dark theme logo that i provided

Requirements
Must have
• Marco Peltieri, 16045518293, RWTFittings@mailbox-demo.com, 1407-5194 Linden Row Burnaby BC, V5H 2K9, Owner & Manager

```html
<!DOCTYPE html>
<html lang="en">
<head>
<meta charset="utf-8">
<title>RWT Fittings Ltd — Business Cards</title>
<link rel="stylesheet" href="https://fonts.googleapis.com/css2?family=Open+Sans:wght@400;600;700&display=swap">
<style>
  :root {
    --canvas: #232323;
    --card: #1f1f24;
    --blue: #29abe2;
    --grey: #8f8f94;
    --white: #f2f2f2;
    --rule: #8a8a8a;
    --photo-dark: #1c1a18;
    --photo-mid: #3a3632;
  }
  * { margin: 0; padding: 0; box-sizing: border-box; }
  html, body {
    width: 1200px; height: 780px; overflow: hidden;
    background: var(--canvas);
    font-family: "Open Sans", Arial, sans-serif;
  }
  .sheet {
    position: relative; width: 1200px; height: 780px;
    display: flex; align-items: center; justify-content: center; gap: 70px;
  }
  .card {
    position: relative; width: 500px; height: 286px; overflow: hidden;
    box-shadow: 0 14px 30px rgba(0,0,0,.55);
  }

  /* Contact side */
  .card--contact { background: var(--card); }
  .brand {
    display: flex; align-items: center; gap: 10px;
    font-weight: 700; color: var(--blue); letter-spacing: .3px; white-space: nowrap;
  }
  .brand__mark { width: 14px; height: 14px; background: var(--blue); flex: none; }
  .card--contact .brand { position: absolute; left: 34px; top: 84px; font-size: 19px; }
  .divider {
    position: absolute; left: 248px; top: 56px; width: 1px; height: 150px;
    background: var(--rule);
  }
  .person { position: absolute; left: 266px; top: 56px; width: 222px; }
  .person__name { font-size: 24px; font-weight: 700; line-height: 1.1; white-space: nowrap; }
  .person__first { color: var(--blue); }
  .person__last { color: var(--grey); }
  .person__title { color: var(--white); font-size: 13px; font-weight: 600; margin-top: 4px; }
  .contact-list { list-style: none; margin-top: 16px; }
  .contact-list li {
    display: flex; align-items: center; gap: 7px;
    color: var(--white); font-size: 12px; line-height: 1.8; white-space: nowrap;
  }
  .contact-list svg { width: 12px; height: 12px; flex: none; }
  .address {
    position: absolute; left: 34px; bottom: 34px;
    color: var(--white); font-size: 13px; white-space: nowrap;
  }

  /* Brand side */
  .card--brand { display: flex; align-items: center; justify-content: center; }
  .card__photo {
    position: absolute; inset: 0;
    background: radial-gradient(ellipse at 70% 55%, var(--photo-mid), var(--photo-dark) 75%);
  }
  .card--brand .brand { position: relative; font-size: 34px; gap: 14px; }
  .card--brand .brand__mark { width: 24px; height: 24px; }
</style>
</head>
<body>
<main class="sheet">
  <section class="card card--contact" aria-label="Contact side">
    <div class="brand"><span class="brand__mark"></span>RWT Fittings Ltd</div>
    <div class="divider"></div>
    <div class="person">
      <p class="person__name"><span class="person__first">Marco</span> <span class="person__last">Peltieri</span></p>
      <p class="person__title">Owner &amp; Manager</p>
      <ul class="contact-list">
        <li>
          <svg viewBox="0 0 24 24" aria-hidden="true"><path fill="#29abe2" d="M6.6 10.8a15.1 15.1 0 0 0 6.6 6.6l2.2-2.2a1 1 0 0 1 1-.25 11.4 11.4 0 0 0 3.6.57 1 1 0 0 1 1 1V20a1 1 0 0 1-1 1A17 17 0 0 1 3 4a1 1 0 0 1 1-1h3.5a1 1 0 0 1 1 1c0 1.25.2 2.45.57 3.57a1 1 0 0 1-.25 1z"/></svg>
          +1 (604) 551-8293
        </li>
        <li>
          <svg viewBox="0 0 24 24" aria-hidden="true"><rect x="2" y="5" width="20" height="14" rx="2" fill="#29abe2"/><path d="M3 6l9 7 9-7" fill="none" stroke="#1f1f24" stroke-width="2"/></svg>
          RWTFittings@mailbox-demo.com
        </li>
        <li>
          <svg viewBox="0 0 24 24" aria-hidden="true"><circle cx="12" cy="12" r="10" fill="#29abe2"/><path d="M2 12h20M12 2c3 3 3 17 0 20M12 2c-3 3-3 17 0 20" fill="none" stroke="#1f1f24" stroke-width="1.5"/></svg>
          www.website.com
        </li>
      </ul>
    </div>
    <p class="address">1407-5194 Linden Row Burnaby BC, V5H 2K9</p>
  </section>

  <section class="card card--brand" aria-label="Brand side">
    <div class="card__photo" role="img" aria-label="Dim photograph of a modern office interior with plants"></div>
    <div class="brand"><span class="brand__mark"></span>RWT Fittings Ltd</div>
  </section>
</main>
</body>
</html>
```